House flipping business web site needed

pinecrestholdingsgroup.example.
I am a residential developer in Northern NJ and I am looking for a fresh new updated website. I have an intro video about my company being made now. I don't update it very often but I want an easy format that I can add update photos to on projects I have worked on or homes I renovate for sale.

Target Market(s)

investors into my projects so a portfolio , people looking to sell their homes to me.

Industry/Entity Type

Real Estate Development

Number of Pages Required

4 page

Font styles to use
Serif

Colors
33b8a4
39a9d7
cadf82

Requirements
Must have
• space for an intro video about my company
• a portfolio with pictures and information about each project
• Markets we serve- Morris County, NJ
• My logo- already created
• SEO
• Yes I would like this to function over all platforms. Phone, computer, all platforms.
• history and background page
• I am looking for a completed page that I can upload to the site that hosts my website
Nice to have
• I want something creative, easy to navigate. modern.

```html
<!DOCTYPE html>
<html lang="en">
<head>
<meta charset="utf-8">
<title>Pinecrest Holdings Group</title>
<link rel="stylesheet" href="https://fonts.googleapis.com/css2?family=Arimo:wght@400;700&family=Dancing+Script:wght@500&family=Lora:ital@1&family=Lato:wght@400;700&display=swap">
<style>
:root{
  --teal:#33b8a4;
  --teal-dark:#23957f;
  --sky:#39a9d7;
  --sky-dark:#2a86b8;
  --lime:#a9c957;
  --ink:#1c1c1c;
  --muted:#555;
  --soft:#8a8a8a;
  --topbar:#f2f3f5;
  --projects-bg:#eef0ea;
  --white:#fff;
}
*{margin:0;padding:0;box-sizing:border-box}
html,body{width:1200px;height:2683px;overflow:hidden;background:var(--white)}
body{position:relative;font-family:"Arimo",Arial,sans-serif;color:var(--ink)}
.abs{position:absolute}

/* top bar */
.topbar{left:0;top:0;width:1200px;height:79px;background:var(--topbar)}
.contact-item{top:28px;font-size:15px;font-weight:700;display:flex;align-items:center;gap:12px}
.contact-item .ico{width:22px;height:22px;border-radius:5px;display:flex;align-items:center;justify-content:center}
.social{top:26px;left:903px;display:flex;gap:12px}
.social span{width:28px;height:28px;border:1.5px solid var(--teal);border-radius:50%;display:block}

/* nav */
.nav{left:0;top:79px;width:1200px;height:52px;background:linear-gradient(#4cb6e0,#2f9bcb)}
.nav a{position:absolute;top:0;height:52px;line-height:52px;color:var(--white);font-size:14px;text-decoration:none;text-transform:uppercase}
.nav .active{background:var(--sky-dark);padding:0 24px}
.brand{left:510px;top:0;width:178px;height:157px;background:var(--white);border-radius:0 0 30px 30px;box-shadow:0 3px 8px rgba(0,0,0,.15);text-align:center;padding-top:50px}
.brand .dot{width:34px;height:34px;border-radius:50%;background:var(--sky);margin:0 auto 10px}
.brand .name{font-size:17px;font-weight:700;color:var(--sky-dark);letter-spacing:1px;line-height:1.2}

/* hero */
.hero{left:0;top:131px;width:1200px;height:518px;background:linear-gradient(160deg,#5c7443 0%,#3d5529 45%,#4c6d2e 75%,#2e421d 100%)}
.hero-kicker{left:98px;top:266px;font-family:"Dancing Script",cursive;font-size:25px;color:var(--white)}
.hero-title{left:98px;top:308px;font-size:40px;font-weight:700;color:var(--white)}
.hero-text{left:98px;top:370px;width:520px;font-size:15px;line-height:29px;color:var(--white)}
.btn{display:inline-block;background:var(--teal);color:var(--white);font-size:15px;border:2px solid rgba(255,255,255,.7);border-radius:3px}
.hero-btn{left:98px;top:461px;width:140px;height:45px;line-height:41px;text-align:center}
.arrow{top:348px}

/* feature grid */
.tile{display:flex;flex-direction:column;align-items:center;text-align:center;color:var(--white)}
.tile h3{font-size:17px;margin:14px 0 8px}
.tile p{font-size:12px;line-height:20px;width:230px}
.tile .more{font-size:12px;font-weight:700;margin-top:12px}
.about h2{font-size:29px;font-weight:700;color:var(--ink);margin:4px 0 16px}
.script{font-family:"Dancing Script",cursive;color:var(--teal);font-size:20px}
.about p{font-size:12.5px;line-height:23px;color:var(--muted);width:440px;text-align:center}
.about .btn{margin-top:16px;font-size:13px;padding:8px 14px;border:none;border-radius:3px}
.video-label{left:642px;top:940px;color:var(--white)}
.video-label b{font-size:15px;display:block}
.video-label span{font-size:11px}
.play{left:877px;top:1028px;width:50px;height:34px;background:#e52d27;border-radius:8px}

/* sections */
.section-title{left:0;width:1200px;text-align:center;font-size:29px;font-weight:700}
.section-sub{left:0;width:1200px;text-align:center;font-family:"Lora",serif;font-style:italic;font-size:13px;color:var(--soft)}
.market{top:1315px;width:210px;text-align:center}
.market .ring{width:124px;height:124px;margin:0 auto;border-radius:50%;border:3px solid var(--sky);background:#d6eef8;box-shadow:inset 0 0 0 6px var(--white);display:flex;align-items:center;justify-content:center}
.market .ring i{width:74px;height:74px;border-radius:50%;background:#1f8ed0;display:flex;align-items:center;justify-content:center}
.market h4{font-size:16px;margin-top:24px;text-transform:uppercase}
.market p{font-size:12px;line-height:20px;color:var(--muted);margin-top:10px}

.projects{left:0;top:1581px;width:1200px;height:425px;background:var(--projects-bg)}
.projects-title{left:98px;top:1632px;font-size:29px;font-weight:700}
.projects-sub{left:98px;top:1672px;font-size:13px;color:var(--muted)}
.project{top:1720px;width:234px}
.project .photo{height:147px;border:3px solid var(--white);box-shadow:0 1px 3px rgba(0,0,0,.2)}
.project h5{font-size:16px;margin-top:22px}
.project p{font-size:12px;line-height:20px;color:var(--teal);margin-top:8px}

.testimonial{top:2163px;width:466px;display:flex;gap:28px}
.testimonial .portrait{width:122px;height:111px;border:3px solid var(--white);box-shadow:0 1px 4px rgba(0,0,0,.25);flex:none}
.testimonial h6{font-size:15px;font-weight:700;margin-top:4px}
.testimonial .role{font-size:11px;color:var(--soft);margin-top:6px}
.testimonial .role b{color:#f0a030;letter-spacing:1px;margin-left:14px}
.testimonial p{font-size:12px;line-height:22px;color:var(--muted);margin-top:14px;text-align:justify}
.quote{font-family:Georgia,serif;font-size:70px;color:#d5d5d5;line-height:1}

/* footer */
.footer{left:0;top:2337px;width:1200px;height:284px;background:linear-gradient(#3ca4d6,#2f97ca)}
.foot-head{font-size:16px;color:var(--white);top:2405px;text-transform:uppercase}
.foot-list{top:2440px;list-style:none;font-size:13px;color:#e6f4fb;line-height:30px}
.support{left:104px;top:2405px;width:400px;text-align:center;color:var(--white)}
.support .phone{font-family:"Lato",sans-serif;font-size:46px;font-weight:700;margin:12px 0 20px}
.support p{font-size:13px;line-height:26px}
.copyright{left:0;top:2621px;width:1200px;height:62px;background:#1f7fb4;color:var(--white);font-size:13px;text-align:center;line-height:62px}
</style>
</head>
<body>

<div class="abs topbar"></div>
<div class="abs contact-item" style="left:98px">
  <span class="ico" style="background:var(--teal)"><svg width="12" height="12" viewBox="0 0 24 24"><path fill="#fff" d="M6.6 10.8a15 15 0 0 0 6.6 6.6l2.2-2.2c.3-.3.7-.4 1-.2 1.1.4 2.3.6 3.6.6.6 0 1 .4 1 1V20c0 .6-.4 1-1 1A17 17 0 0 1 3 4c0-.6.4-1 1-1h3.5c.6 0 1 .4 1 1 0 1.3.2 2.5.6 3.6.1.3 0 .7-.2 1z"/></svg></span>
  +1 555-014-2270
</div>
<div class="abs contact-item" style="left:286px">
  <span class="ico" style="background:var(--lime)"><svg width="13" height="10" viewBox="0 0 13 10"><rect x=".5" y=".5" width="12" height="9" fill="none" stroke="#fff"/><path d="M.5.5l6 5 6-5" fill="none" stroke="#fff"/></svg></span>
  @pinecrestholdingsgroup
</div>
<div class="abs social"><span></span><span></span><span></span><span></span><span></span><span></span></div>

<nav class="abs nav">
  <a class="active" style="left:98px">Home</a>
  <a style="left:209px">About Us</a>
  <a style="left:322px">Services</a>
  <a style="left:433px">Blog</a>
  <a style="left:720px">Portfolio</a>
  <a style="left:842px">Testimonial</a>
  <a style="left:975px">Contact</a>
  <a style="left:1060px">|</a>
  <a style="left:1084px"><svg width="15" height="15" viewBox="0 0 15 15" style="vertical-align:middle"><circle cx="6" cy="6" r="4.5" fill="none" stroke="#fff" stroke-width="2"/><path d="M9.5 9.5l4 4" stroke="#fff" stroke-width="2.4"/></svg></a>
</nav>
<div class="abs brand"><div class="dot"></div><div class="name">PINECREST<br>HOLDINGS</div></div>

<div class="abs hero" role="img" aria-label="Photo of an old clapboard cottage among green trees and lawn"></div>
<div class="abs hero-kicker">Investing In Our Neighborhoods</div>
<div class="abs hero-title">PINECREST HOLDINGS GROUP</div>
<p class="abs hero-text">We will help you get out of your unwanted home We bring excellence to the home buying and renovation business.</p>
<a class="abs btn hero-btn">Read More Info</a>
<svg class="abs arrow" style="left:30px" width="22" height="80" viewBox="0 0 22 80"><path d="M20 2L2 40l18 38" fill="none" stroke="#fff" stroke-width="2"/></svg>
<svg class="abs arrow" style="left:1148px" width="22" height="80" viewBox="0 0 22 80"><path d="M2 2l18 38L2 78" fill="none" stroke="#fff" stroke-width="2"/></svg>

<!-- feature grid -->
<div class="abs tile" style="left:0;top:653px;width:299px;height:259px;background:var(--lime);padding-top:42px">
  <svg width="52" height="46" viewBox="0 0 52 46"><path d="M26 43S3 29 3 14A11 11 0 0 1 26 9a11 11 0 0 1 23 5c0 15-23 29-23 29z" fill="none" stroke="#fff" stroke-width="3"/></svg>
  <h3>NEIGHBORHOOD</h3>
  <p>We only buy and renovate homes in our neighborhoods right here in the Morris County, NJ area</p>
  <span class="more" style="color:#6f8d2a">» Read More</span>
</div>
<div class="abs" style="left:302px;top:653px;width:297px;height:259px;background:linear-gradient(#cfe3f3 0%,#9bb3c2 40%,#6f5a3e 60%,#5b6f82 100%)" role="img" aria-label="Photo of a calm lake with trees on the far shore"></div>
<div class="abs tile about" style="left:603px;top:653px;width:597px;height:259px;padding-top:32px">
  <span class="script">Welcome to Pinecrest Holdings</span>
  <h2>ABOUT OUR BUSINESS</h2>
  <p>We only buy and renovate homes in our neighborhoods right here in the Morris County, NJ area. Is a house in your neighborhood an eyesore? Is it vacant, boarded up and a hazard to the neighborhood?</p>
  <a class="btn">READ MORE</a>
</div>

<div class="abs" style="left:0;top:915px;width:299px;height:258px;background:linear-gradient(#c58a4a 0%,#7c8aa0 35%,#3f5f8a 60%,#b8473f 100%)" role="img" aria-label="Photo of a family by a lake in autumn"></div>
<div class="abs tile" style="left:302px;top:915px;width:297px;height:258px;background:var(--teal);padding-top:38px">
  <svg width="40" height="42" viewBox="0 0 40 42"><rect x="10" y="2" width="22" height="14" rx="2" fill="#fff" transform="rotate(12 21 9)"/><path d="M4 24h12l6 6h10v8H12l-8-4z" fill="#fff"/></svg>
  <h3>FINANCING</h3>
  <p>We can close quickly and we buy with CashWe can close quickly and we buy with CashWe can close quickly</p>
  <span class="more" style="color:#16735f">» Read More</span>
</div>
<div class="abs" style="left:603px;top:915px;width:597px;height:258px;background:linear-gradient(#6f8f5a 0%,#c9ccc6 35%,#8e8c84 65%,#5f5a50 100%)" role="img" aria-label="Video still of a renovated house with a deck and stone wall"></div>
<div class="abs video-label"><b>INTRODUCTION VIDEO</b><span>Pinecrest Holdings Group</span></div>
<div class="abs play"><svg width="50" height="34" viewBox="0 0 50 34"><path d="M20 10l12 7-12 7z" fill="#fff"/></svg></div>

<!-- markets -->
<h2 class="abs section-title" style="top:1225px">MARKETS WE SERVE</h2>
<div class="abs section-sub" style="top:1266px">Investing In Our Neighborhoods</div>

<div class="abs market" style="left:79px"><div class="ring"><i><svg width="38" height="34" viewBox="0 0 38 34"><path d="M3 17L19 3l16 14M8 13v18h22V13" fill="none" stroke="#fff" stroke-width="3"/></svg></i></div><h4>Renovate Homes</h4><p>We are a team of experienced in<br>home buyers renovators</p></div>
<div class="abs market" style="left:287px"><div class="ring"><i><svg width="34" height="34" viewBox="0 0 34 34" fill="#fff"><rect x="3" y="4" width="14" height="28"/><rect x="19" y="13" width="12" height="19"/></svg></i></div><h4>Redevelopment</h4><p>We are a team of experienced in<br>home buyers renovators</p></div>
<div class="abs market" style="left:494px"><div class="ring"><i><svg width="38" height="32" viewBox="0 0 38 32" fill="#fff"><path d="M2 15L19 2l17 13h-5v15H7V15z"/></svg></i></div><h4>Newly Built Home</h4><p>We are a team of experienced in<br>home buyers renovators</p></div>
<div class="abs market" style="left:701px"><div class="ring"><i><svg width="40" height="30" viewBox="0 0 40 30" fill="#fff"><circle cx="20" cy="8" r="6"/><circle cx="8" cy="11" r="4.5"/><circle cx="32" cy="11" r="4.5"/><path d="M10 29a10 10 0 0 1 20 0z"/><path d="M0 29a8 8 0 0 1 12-7v7zM40 29a8 8 0 0 0-12-7v7z"/></svg></i></div><h4>Optional Membership</h4><p>We are a team of experienced in<br>home buyers renovators</p></div>
<div class="abs market" style="left:909px"><div class="ring"><i><svg width="30" height="36" viewBox="0 0 30 36"><rect x="2" y="4" width="26" height="30" rx="2" fill="none" stroke="#fff" stroke-width="3"/><path d="M7 14l2 2 4-4M7 23l2 2 4-4M16 14h7M16 23h7" stroke="#fff" stroke-width="2" fill="none"/></svg></i></div><h4>Organized Chaos</h4><p>We are a team of experienced in<br>home buyers renovators</p></div>

<!-- projects -->
<div class="abs projects"></div>
<h2 class="abs projects-title">RECENT PROJECTS</h2>
<div class="abs projects-sub">We are a team of experienced home buyers and renovators</div>
<div class="abs project" style="left:98px"><div class="photo" role="img" aria-label="Photo of a renovated two-storey house in Rockaway" style="background:linear-gradient(#c9d2da,#a89a86 55%,#6f6a55)"></div><h5>ROCKAWAY, NJ</h5><p>Many upgrades to this home, Added a new full bath, family room, office</p></div>
<div class="abs project" style="left:356px"><div class="photo" role="img" aria-label="Photo of a grey colonial house in Denville" style="background:linear-gradient(#9fc0da,#8c9186 55%,#5d7a3a)"></div><h5>DENVILLE, NJ</h5><p>Many upgrades to this home, Added a new full bath, family room, office</p></div>
<div class="abs project" style="left:612px"><div class="photo" role="img" aria-label="Photo of a small blue cottage in Boonton" style="background:linear-gradient(#4d6e32,#7b9fae 55%,#5e8a35)"></div><h5>BOONTON, NJ</h5><p>Many upgrades to this home, Added a new full bath, family room, office</p></div>
<div class="abs project" style="left:869px"><div class="photo" role="img" aria-label="Photo of a wooded house with a deck in New Jersey" style="background:linear-gradient(#3f5a2c,#6b4a34 60%,#4e6b33)"></div><h5>NEW JERSEY.</h5><p>Many upgrades to this home, Added a new full bath, family room, office</p></div>

<!-- testimonials -->
<h2 class="abs section-title" style="top:2061px">OUR CLIENT TESTIMONIAL</h2>
<div class="abs section-sub" style="top:2102px">What Our Client Says About us</div>
<div class="abs testimonial" style="left:98px">
  <div class="portrait" role="img" aria-label="Portrait photo of a client" style="background:linear-gradient(#c9b9a6,#8a6b52)"></div>
  <div><div style="display:flex;justify-content:space-between"><div><h6>MARA QUINN ELLIS</h6><div class="role">Customers<b>★★★★★</b></div></div><span class="quote">”</span></div>
  <p style="margin-top:0">Contrary to popular belief, Lorem Ipsum is not simply random text. It has roots in a piece of classical Latin literature from 45 BC, making it over 2000 years old.</p></div>
</div>
<div class="abs testimonial" style="left:637px">
  <div class="portrait" role="img" aria-label="Portrait photo of a client" style="background:linear-gradient(#7ea9c9,#d8b98e)"></div>
  <div><div style="display:flex;justify-content:space-between"><div><h6>MARA QUINN ELLIS</h6><div class="role">Customers<b>★★★★★</b></div></div><span class="quote">”</span></div>
  <p style="margin-top:0">Contrary to popular belief, Lorem Ipsum is not simply random text. It has roots in a piece of classical Latin literature from 45 BC, making it over 2000 years old.</p></div>
</div>

<!-- footer -->
<footer class="abs footer"></footer>
<div class="abs support">
  <div style="font-size:16px">SUPPORT</div>
  <div class="phone">+1 555-014-2270</div>
  <p>@pinecrestholdingsgroup<br>service@pinecrestholdingsgroup.example</p>
</div>
<div class="abs foot-head" style="left:581px">Quick Link</div>
<ul class="abs foot-list" style="left:581px"><li>Team</li><li>Reviews</li><li>Blog</li><li>Contact</li></ul>
<div class="abs foot-head" style="left:765px">Information</div>
<ul class="abs foot-list" style="left:765px"><li>Terms and Condition</li><li>Privacy policy</li><li>Site Map</li></ul>
<div class="abs foot-head" style="left:973px">Company</div>
<ul class="abs foot-list" style="left:973px"><li>Why us</li><li>Contact</li><li>Customers</li><li>Affiliates</li></ul>
<div class="abs copyright">Copyrights@2016Company Name, All rights Reseve</div>

</body>
</html>
```